KLV Plant Services

We are a heavy diesel mechanical business with additional air con certificates, remapping engine rebuilt

Contact Information for Business Card

Company Name, Director Name, Managing Director, Contact details, email and website

Font styles to use
Serif
Script

```html
<!DOCTYPE html>
<html lang="en">
<head>
<meta charset="utf-8">
<title>KLV Plant Services – Business Card</title>
<link href="https://fonts.googleapis.com/css2?family=Arimo:wght@400;700&display=swap" rel="stylesheet">
<style>
  :root {
    --backdrop: #7b7b7b;
    --navy: #06065e;
    --navy-soft: #2a2a8f;
    --ink: #1a1a1a;
    --grey-text: #555555;
    --paper: #f4f4f6;
    --arc-black: #050505;
  }
  * { margin: 0; padding: 0; box-sizing: border-box; }
  html, body {
    width: 1200px; height: 900px; overflow: hidden;
    background: var(--backdrop);
    font-family: "Arimo", Arial, sans-serif;
  }
  .stage {
    width: 1200px; height: 900px;
    display: flex; flex-direction: column;
    align-items: center; justify-content: center;
    gap: 60px;
  }
  .card {
    width: 560px; height: 320px;
    border-radius: 22px;
    position: relative; overflow: hidden;
    box-shadow: 0 6px 18px rgba(0,0,0,0.25);
  }
  .card--back {
    background: var(--navy);
    display: flex; align-items: center; justify-content: center;
  }
  .brand-mark {
    display: flex; align-items: center; gap: 14px;
    color: var(--navy-soft);
    font-weight: 700; font-size: 30px; letter-spacing: 0.5px;
  }
  .brand-mark__dot {
    width: 22px; height: 22px; border-radius: 50%;
    background: var(--navy-soft);
  }
  .card--front { background: var(--paper); }
  .card__swoosh { position: absolute; inset: 0; }
  .details {
    position: absolute; right: 36px; top: 34px;
    text-align: right; color: var(--ink);
  }
  .details__brand {
    display: flex; align-items: center; justify-content: flex-end; gap: 8px;
    color: var(--navy); font-weight: 700; font-size: 19px;
    margin-bottom: 14px;
  }
  .details__brand-dot {
    width: 12px; height: 12px; border-radius: 50%; background: var(--navy);
  }
  .details__name { color: var(--navy); font-weight: 700; font-size: 21px; }
  .details__role { color: var(--grey-text); font-size: 13px; margin-top: 2px; }
  .details__address { font-size: 13px; line-height: 1.35; margin-top: 16px; }
  .contact-list { list-style: none; font-size: 13px; line-height: 1.45; margin-top: 12px; }
  .contact-list li { display: flex; align-items: center; justify-content: flex-end; gap: 5px; }
  .contact-list svg { width: 11px; height: 11px; fill: var(--navy); }
</style>
</head>
<body>
<main class="stage">
  <section class="card card--back" aria-label="Card back">
    <div class="brand-mark">
      <span class="brand-mark__dot"></span>
      <span class="brand-mark__name">KLV Plant Services</span>
    </div>
  </section>

  <section class="card card--front" aria-label="Card front">
    <svg class="card__swoosh" viewBox="0 0 560 320" preserveAspectRatio="none" aria-hidden="true">
      <path d="M0,26 C150,18 250,120 216,320 L0,320 Z" fill="var(--navy)"/>
      <path d="M0,26 C150,18 250,120 216,320 L236,320 C268,110 160,4 0,8 Z" fill="var(--arc-black)"/>
      <path d="M0,17 C155,10 258,118 226,320" fill="none" stroke="#ffffff" stroke-width="1.5"/>
      <path d="M0,8 C160,4 268,110 236,320 L246,320 C280,104 165,-4 0,0 Z" fill="var(--navy)"/>
    </svg>

    <div class="details">
      <div class="details__brand">
        <span class="details__brand-dot"></span>
        <span>KLV Plant Services</span>
      </div>
      <p class="details__name">Daniel Marsh</p>
      <p class="details__role">Managing Director</p>
      <p class="details__address">2190 Harrow Lane<br>Elm Ridge, NY 11020</p>
      <ul class="contact-list">
        <li>(555) 0142-7781
          <svg viewBox="0 0 24 24"><path d="M6.6 10.8a15 15 0 0 0 6.6 6.6l2.2-2.2a1 1 0 0 1 1-.25 11.4 11.4 0 0 0 3.6.6 1 1 0 0 1 1 1V20a1 1 0 0 1-1 1A17 17 0 0 1 3 4a1 1 0 0 1 1-1h3.5a1 1 0 0 1 1 1c0 1.25.2 2.45.6 3.6a1 1 0 0 1-.25 1z"/></svg>
        </li>
        <li>name@KLV.com
          <svg viewBox="0 0 24 24"><path d="M2 5h20v14H2z M2 5l10 8 10-8" stroke="#fff" stroke-width="1.5"/></svg>
        </li>
        <li>www.KLV.com
          <svg viewBox="0 0 24 24"><circle cx="12" cy="12" r="10"/><path d="M2 12h20M12 2c3 3 3 17 0 20M12 2c-3 3-3 17 0 20" stroke="#fff" stroke-width="1.5" fill="none"/></svg>
        </li>
      </ul>
    </div>
  </section>
</main>
</body>
</html>
```